Small Business Broker Business Card Design

A business card design for a small business brokerage, which is a financial service, not unlike real estate brokerage, but for small businesses such as laundromats, pizza shops, restaurants, cleaners etc. The designs should all be simple, more conservative in nature, using the colors and font of the logo. Again, think real estate Brokerage as a business context
Contact Information for Business Card
Name: Glen R. Harlow. Title: Small Business Advisor. Email: g.harlow@bayfieldcapitalworks.example. Mobile: (555) 274-3918. Office: (555) 806-2147. www.bayfieldcapitalworks.example

```html
<!DOCTYPE html>
<html lang="en">
<head>
<meta charset="utf-8">
<title>Bayfield Capital Works – Business Card</title>
<link href="https://fonts.googleapis.com/css2?family=Montserrat:wght@400;500;700;800&display=swap" rel="stylesheet">
<style>
  :root {
    --navy: #1c3a6e;
    --green: #8cc63f;
    --white: #ffffff;
    --ink: #2b2b2b;
    --backdrop: #b3b3b3;
  }
  * { box-sizing: border-box; margin: 0; padding: 0; }
  html, body {
    width: 1200px; height: 900px; overflow: hidden;
    background: var(--backdrop);
    font-family: "Montserrat", Arial, sans-serif;
  }
  .canvas { position: relative; width: 1200px; height: 900px; }
  .card {
    position: absolute; width: 700px; height: 400px;
    box-shadow: 0 6px 18px rgba(0,0,0,.25);
  }
  /* Front */
  .card-front {
    left: 90px; top: 45px; background: var(--white);
    border-bottom: 4px solid var(--green);
  }
  .brand-mark {
    position: absolute; left: 60px; top: 70px;
    width: 150px; height: 150px; background: var(--navy);
  }
  .divider {
    position: absolute; left: 280px; top: 70px;
    width: 2px; height: 170px; background: var(--navy);
  }
  .person { position: absolute; left: 305px; top: 66px; }
  .person-name { color: var(--navy); font-weight: 800; font-size: 30px; line-height: 1.1; }
  .person-title { color: var(--ink); font-weight: 500; font-size: 15px; margin-top: 2px; }
  .contacts { position: absolute; left: 305px; top: 150px; list-style: none; }
  .contacts li {
    display: flex; align-items: center; gap: 10px;
    color: var(--ink); font-size: 15px; line-height: 23px;
  }
  .contacts svg { width: 14px; height: 14px; fill: var(--navy); flex: none; }
  .front-brand { position: absolute; left: 60px; bottom: 40px; }
  .company-name {
    color: var(--navy); font-weight: 800; font-size: 33px;
    letter-spacing: .5px; text-transform: uppercase; white-space: nowrap;
  }
  .tagline {
    color: var(--green); font-weight: 700; font-size: 15.5px;
    letter-spacing: 2px; text-transform: uppercase; margin-top: 4px; white-space: nowrap;
  }
  /* Back */
  .card-back {
    left: 410px; top: 475px; background: var(--green);
    display: flex; flex-direction: column; align-items: center; justify-content: center;
  }
  .back-mark { width: 60px; height: 60px; background: var(--navy); margin-bottom: 18px; }
  .card-back .company-name { font-size: 30px; }
  .card-back .tagline { color: var(--white); font-size: 14px; }
</style>
</head>
<body>
<main class="canvas">
  <section class="card card-front" aria-label="Business card front">
    <div class="brand-mark" aria-hidden="true"></div>
    <div class="divider" aria-hidden="true"></div>
    <div class="person">
      <p class="person-name">Glen R. Harlow</p>
      <p class="person-title">Small Business Advisor</p>
    </div>
    <ul class="contacts">
      <li><svg viewBox="0 0 16 16"><path d="M2 5h12v9H2z M4 2h8v3H4z"/></svg>(555) 806-2147</li>
      <li><svg viewBox="0 0 16 16"><path d="M3 1h4l1 4-2 1.5a9 9 0 0 0 3.5 3.5L11 8l4 1v4c0 1-1 2-2 2A12 12 0 0 1 1 3c0-1 1-2 2-2z"/></svg>(555) 274-3918</li>
      <li><svg viewBox="0 0 16 16"><path d="M1 3h14v10H1z" fill="none" stroke="#1c3a6e" stroke-width="1.6"/><path d="M1 3l7 6 7-6" fill="none" stroke="#1c3a6e" stroke-width="1.6"/></svg>g.harlow@bayfieldcapitalworks.example</li>
      <li><svg viewBox="0 0 16 16"><circle cx="8" cy="8" r="6.5" fill="none" stroke="#1c3a6e" stroke-width="1.6"/><path d="M1.5 8h13M8 1.5c-3 3.5-3 9.5 0 13M8 1.5c3 3.5 3 9.5 0 13" fill="none" stroke="#1c3a6e" stroke-width="1.2"/></svg>www.bayfieldcapitalworks.example</li>
    </ul>
    <div class="front-brand">
      <p class="company-name">Bayfield Capital Works, Inc</p>
      <p class="tagline">Buy or sell a neighborhood business with clarity</p>
    </div>
  </section>

  <section class="card card-back" aria-label="Business card back">
    <div class="back-mark" aria-hidden="true"></div>
    <p class="company-name">Bayfield Capital Works, Inc</p>
    <p class="tagline">Buy or sell a neighborhood business with clarity</p>
  </section>
</main>
</body>
</html>
```